Business Card design for law firm = Brightvale Australia

We are seeking a new design for our business cards.
We are keeping our logo, which is attached.
We need space for
Name
Title
Address is , which is
Level 7
214 Marlowe Street
Sydney NSW 2047
Phone :
Mobile :
Fax :
Email :
DX :
website www.brightvale-example.com.au

Industry/Entity Type

Law Firm / Banking and Finance

Contact Information for Business Card

We are seeking a new design for our business cards. We are keeping our logo. We need space for Name Title Address is Level 7 214 Marlowe Street Sydney NSW 2047 Phone Mobile Fax Email DX website www.brightvale-example.com.au

Colors
0054AA
0677BA
7BADD7
CADEEF
E8F1F8

Requirements
Must have
• see our website for general feel www.brightvale-example.com.au

```html
<!DOCTYPE html>
<html lang="en">
<head>
<meta charset="utf-8">
<title>Brightvale Australia – Business Card</title>
<link rel="stylesheet" href="https://fonts.googleapis.com/css2?family=EB+Garamond:ital,wght@0,400;1,400&display=swap">
<style>
  :root {
    --page-bg: #262626;
    --card-blue-top: #1297cc;
    --card-blue-bottom: #0a83b6;
    --card-white: #f1f1f1;
    --brand-navy: #2a4d9c;
    --ink: #2b2b2b;
    --icon: #1a8cc4;
  }
  * { box-sizing: border-box; margin: 0; padding: 0; }
  html, body {
    width: 1200px; height: 576px; overflow: hidden;
    background: var(--page-bg);
    font-family: "EB Garamond", Georgia, serif;
  }
  .canvas { position: relative; width: 1200px; height: 576px; }

  .card {
    position: absolute;
    border-radius: 10px;
    overflow: hidden;
  }
  .card--back {
    left: 102px; top: 139px; width: 484px; height: 292px;
    background: linear-gradient(180deg, var(--card-blue-top), var(--card-blue-bottom));
  }
  .card--front {
    left: 596px; top: 138px; width: 480px; height: 291px;
    background: var(--card-white);
  }

  .brand-name {
    position: absolute; white-space: nowrap;
    font-size: 29px; line-height: 1; font-weight: 400;
    color: var(--brand-navy);
  }
  .card--back .brand-name { left: 37px; top: 217px; }
  .card--front .brand-name { right: 36px; top: 216px; }

  .person { position: absolute; right: 36px; top: 37px; text-align: right; color: var(--brand-navy); }
  .person__name { font-size: 21px; line-height: 24px; }
  .person__title { font-size: 12.5px; line-height: 16px; font-style: italic; color: var(--ink); }

  .address {
    position: absolute; left: 31px; top: 162px;
    font-size: 12.5px; line-height: 16px; color: var(--ink); font-style: normal;
  }
  .contact-list {
    position: absolute; left: 31px; top: 202px; list-style: none;
    font-size: 12.5px; line-height: 15.7px; color: var(--ink);
  }
  .contact-list li { display: flex; align-items: center; }
  .contact-list svg { width: 9px; height: 9px; margin: 0 10px 0 5px; fill: var(--icon); flex: none; }
</style>
</head>
<body>
<div class="canvas">

  <section class="card card--back" aria-label="Card back">
    <div class="brand-name">Brightvale</div>
  </section>

  <section class="card card--front" aria-label="Card front">
    <div class="person">
      <div class="person__name">Sam Hartley</div>
      <div class="person__title">Managing Director</div>
    </div>

    <address class="address">
      Level 7 214 Marlowe St<br>
      Sydney NSW 2047
    </address>

    <ul class="contact-list">
      <li>
        <svg viewBox="0 0 10 10" aria-label="Phone"><path d="M1 3.5C1 2 3 1 5 1s4 1 4 2.5L7.5 4.2 7 3H3L2.5 4.2zM2.5 5h5L8.5 9h-7z"/></svg>
        02 9000 0147
      </li>
      <li>
        <svg viewBox="0 0 10 10" aria-label="Fax"><path d="M3 1h4v2H3zM1 3.5h8V7.5H7.5V6h-5v1.5H1zM3 6.7h4V9H3z"/></svg>
        02 9000 0148
      </li>
      <li>
        <svg viewBox="0 0 10 10" aria-label="Email"><path d="M0.5 2h9v6h-9zM1.5 3v.3L5 5.8l3.5-2.5V3L5 5.3z"/></svg>
        sam.hartley@brightvale-example.com.au
      </li>
      <li>
        <svg viewBox="0 0 10 10" aria-label="Website"><path d="M5 .8A4.2 4.2 0 1 0 5 9.2 4.2 4.2 0 0 0 5 .8zm0 1a3.2 3.2 0 0 1 3.1 2.7H1.9A3.2 3.2 0 0 1 5 1.8zM1.9 5.5h6.2A3.2 3.2 0 0 1 1.9 5.5z"/></svg>
        www.brightvale-example.com.au
      </li>
    </ul>

    <div class="brand-name">Brightvale</div>
  </section>

</div>
</body>
</html>
```